Business Card Design

Hello,
I try and keep my business card fresh and current. So about every year i get a new one. This year I'd like something with a white background and black lettering.
Before you start - I do not want my phone number or any other description on the card other than my url and my email.

I'd like a double sided business card with
TomFarrow.com on one side

and

Tom@TomFarrow.com on the other side of the card

Thinking very minimalistic and modern.
I don't have a particular font i mind or how to capitalize my name or website. This card will lead people to my new website that is being designed to showcase my photography and music.

* Initial thought was the front side of the card having a grid-like pattern built out of dashes or periods, with my website sitting within the pattern and on the back side my email on a stark white background. But that might look completely lame - haha.

I'm looking forward to seeing what you come up with.

thank you,
- tom farrow
Updates

Project Deadline Extended
Reason: Want to spend some more time with the designs and add a little $. thanks for all the designs - tom

Project Deadline Extended

Wanted to add a little $ and spend some more time with the designs.

big thanks to all who have submitted work 

- tom

Industry/Entity Type

Business

Contact Information for Business Card

www.tomfarrow.com
tom@tomfarrow.com

Colors
000000
ffffff

Requirements
Must have
• tomfarrow.com
tom@tomfarrow.com
Should not have
• phone number
any description of what i do, photography or music

```html
<!DOCTYPE html>
<html lang="en">
<head>
<meta charset="utf-8">
<title>TomFarrow.com — Business Card</title>
<link rel="stylesheet" href="https://fonts.googleapis.com/css2?family=Open+Sans:wght@700&display=swap">
<style>
  :root {
    --page-bg: #e9e7e3;
    --card-dark: #2e2e2e;
    --card-dark-deep: #1c1c1c;
    --card-dark-light: #4a4a4a;
    --card-white: #ffffff;
    --card-white-shade: #ececec;
    --ink-black: #000000;
    --ink-white: #ffffff;
    --shadow: rgba(0, 0, 0, 0.22);
  }
  html, body {
    margin: 0;
    padding: 0;
    width: 704px;
    height: 1200px;
    overflow: hidden;
    background: var(--page-bg);
  }
  .sheet {
    position: relative;
    width: 704px;
    height: 1200px;
  }
  .card-slot {
    position: relative;
    width: 704px;
    height: 600px;
    display: flex;
    align-items: center;
    justify-content: center;
  }
  .card {
    position: relative;
    width: 290px;
    height: 500px;
    border-radius: 22px;
    box-shadow: 0 10px 28px var(--shadow);
    overflow: hidden;
  }
  .card--front {
    background: linear-gradient(135deg, var(--card-dark-light) 0%, var(--card-dark) 45%, var(--card-dark-deep) 100%);
  }
  .card--back {
    background: linear-gradient(160deg, var(--card-white) 0%, var(--card-white) 55%, var(--card-white-shade) 100%);
  }
  .card__pattern {
    position: absolute;
    inset: 0;
  }
  .card__text {
    position: absolute;
    top: 26px;
    right: 20px;
    writing-mode: vertical-rl;
    transform: rotate(180deg);
    font-family: "Open Sans", sans-serif;
    font-weight: 700;
    font-size: 22px;
    letter-spacing: 0.2px;
    white-space: nowrap;
    margin: 0;
  }
  .card--front .card__text { color: var(--ink-white); }
  .card--back .card__text { color: var(--ink-black); }
</style>
</head>
<body>
  <main class="sheet">
    <section class="card-slot">
      <div class="card card--front">
        <div class="card__pattern" role="img" aria-label="Fine diagonal grid pattern of thin light lines over dark grey"></div>
        <p class="card__text">TomFarrow.com</p>
      </div>
    </section>
    <section class="card-slot">
      <div class="card card--back">
        <p class="card__text">Tom@TomFarrow.com</p>
      </div>
    </section>
  </main>
</body>
</html>
```